1 Page for Computer Repair Website

Looking for a 1 page website with a design that compliments the business card and pamphlet that have already been made (attached files). It should look business professional and easy to read. Email and phone number should be somewhere near the top of the website, visible when the page loads. I don't want any forms for people to mess with. No "Contact Us" form or entering in email for newsletter. Customers will just be looking at this site to confirm we are professionals and have our business in order.

Target Market(s)

Home and small business

Industry/Entity Type

Computer Repair

Coding

Coded - Design and coding required

Number of Pages Required

1 page

Font styles to use
Other font styles liked:
• Helvetica variations used in pamphlet and card

Colors
0455a3
cfdeed
85abd2
3276b5
85cae6
ffffff

Requirements
Must have
• Compliment the pamphlet and business card in color choices and font use. Pleasing to the eye and easy to read through categories and text.
Should not have
• Forms. No "enter name and email here" or anything of the sort.

```html
<!DOCTYPE html>
<html lang="en">
<head>
<meta charset="utf-8">
<title>Quikbit Computer Service</title>
<link href="https://fonts.googleapis.com/css2?family=Open+Sans:wght@400;600;700&display=swap" rel="stylesheet">
<style>
:root{
  --blue:#0455a3;
  --blue-mid:#3276b5;
  --blue-soft:#85abd2;
  --sky:#85cae6;
  --ice:#cfdeed;
  --white:#ffffff;
  --ink:#2b2f36;
  --grey:#6b7078;
  --panel:#eef0f3;
  --line:#dde1e6;
}
*{box-sizing:border-box;margin:0;padding:0}
html,body{width:703px;height:1200px;overflow:hidden;background:var(--white)}
body{font-family:"Open Sans",Helvetica,Arial,sans-serif;color:var(--ink);font-size:7px;line-height:1.55}
.page{position:relative;width:703px;height:1200px}

.topbar{height:22px;display:flex;justify-content:space-between;align-items:center;padding:0 20px 0 62px;border-bottom:1px solid var(--line);color:var(--grey);font-size:6.5px}
.topbar .contact span{margin-right:14px}
.social{display:flex;gap:3px}
.social i{display:block;width:14px;height:14px;background:var(--blue-mid)}

.header{height:62px;display:flex;justify-content:space-between;align-items:center;padding:0 22px 0 62px}
.brand{display:flex;align-items:center;gap:6px}
.brand .mark{width:10px;height:10px;background:var(--blue)}
.brand .name{font-size:22px;font-weight:700;color:var(--blue);letter-spacing:.5px;line-height:1}
.brand small{display:block;font-size:6px;color:var(--grey);letter-spacing:1px;margin-top:2px}
.nav{display:flex;gap:22px;font-size:6px;font-weight:600;text-transform:uppercase;color:var(--grey)}
.nav .active{color:var(--blue)}

.hero{position:relative;height:238px;background:linear-gradient(90deg,#f4f5f7,#e7eaee)}
.hero-text{position:absolute;left:62px;top:42px;width:270px}
.hero-text h1{font-size:26px;font-weight:400;color:var(--blue);line-height:1}
.hero-text h2{font-size:12px;font-weight:400;letter-spacing:.6px;color:var(--ink);margin:8px 0 10px;border-bottom:1px solid var(--line);padding-bottom:8px}
.hero-text p{color:var(--grey);font-size:6.5px}
.hero-photo{position:absolute;right:60px;top:12px;width:270px;height:226px;background:linear-gradient(135deg,#c9d4de,#8a9fb4 60%,#5b6f85)}

.features{position:relative;height:148px;background:var(--blue);display:flex;padding:0 50px}
.feature{flex:1;text-align:center;color:var(--white);padding:0 12px}
.feature .icon{width:46px;height:46px;border-radius:50%;background:var(--blue-mid);border:3px solid var(--white);margin:-23px auto 10px;display:flex;align-items:center;justify-content:center}
.feature h3{font-size:6.5px;font-weight:700;text-transform:uppercase;color:var(--ice);margin-bottom:5px}
.feature p{font-size:6px;color:var(--ice)}
.feature a{display:inline-block;margin-top:6px;color:var(--white);font-size:6.5px;text-decoration:none}

.why{display:flex;height:184px;padding:26px 62px 0}
.why-art{width:140px;height:140px;background:linear-gradient(160deg,#f2c79a,#c5722c 55%,#5a6470);border-radius:4px}
.why-body{flex:1;padding-left:34px}
h2.title{font-size:14px;font-weight:700;text-transform:uppercase;color:var(--ink);margin-bottom:6px}
.why-body>p{color:var(--grey);font-size:6.5px;margin-bottom:8px}
.ticks{list-style:none}
.ticks li{display:flex;align-items:center;gap:6px;padding:4px 0;border-bottom:1px solid var(--line);color:var(--grey);font-size:6.5px}
.ticks li::before{content:"";width:6px;height:6px;border-radius:50%;background:var(--blue-mid)}

.about{height:194px;background:var(--panel);display:flex;padding:22px 62px 0}
.about-main{flex:1;padding-right:30px;border-right:1px solid var(--line)}
.about-main p{color:var(--grey);font-size:6.5px;margin-bottom:7px}
.btn{display:inline-block;background:var(--blue);color:var(--white);font-size:6.5px;font-weight:700;padding:7px 14px;text-transform:uppercase;letter-spacing:.5px}
.services{width:160px;padding-left:28px}
.services ul{list-style:none}
.services li{font-size:6.5px;color:var(--grey);padding:3px 0 3px 9px;border-bottom:1px solid var(--line);position:relative}
.services li::before{content:"";position:absolute;left:0;top:7px;width:4px;height:4px;background:var(--blue-mid)}

.promos{display:flex;gap:24px;height:170px;padding:24px 62px 0}
.promo{flex:1;display:flex;gap:12px}
.promo .photo{width:92px;height:92px;flex:none;background:linear-gradient(135deg,#d8dde3,#8093a6)}
.promo h4{font-size:8.5px;font-weight:600;color:var(--blue);margin-bottom:5px}
.promo p{font-size:6.3px;color:var(--grey)}

.footer{position:absolute;left:0;bottom:0;width:703px;height:134px;background:var(--blue);color:var(--ice);text-align:center;padding-top:36px}
.footer nav{display:flex;justify-content:center;gap:14px;font-size:6.5px}
.footer nav span+span::before{content:"|";margin-right:14px;color:var(--blue-soft)}
.footer .round{display:flex;justify-content:center;gap:6px;margin:14px 0}
.footer .round i{display:block;width:14px;height:14px;border-radius:50%;border:1px solid var(--blue-soft)}
.footer small{font-size:6px;color:var(--blue-soft)}
</style>
</head>
<body>
<div class="page">
  <div class="topbar">
    <div class="contact"><span>✉ hello@quikbit.example</span><span>☎ Phone: (555) 014-2290</span></div>
    <div class="social"><i></i><i></i><i></i><i></i></div>
  </div>

  <header class="header">
    <div class="brand"><span class="mark"></span><div><div class="name">QUIKBIT</div><small>Computer Services</small></div></div>
    <nav class="nav"><span class="active">Home</span><span>About Us</span><span>Services</span><span>Features</span><span>Why Choose Us</span><span>Products</span><span>Contact Us</span></nav>
  </header>

  <section class="hero">
    <div class="hero-text">
      <h1>QUIKBIT</h1>
      <h2>COMPUTER SERVICE &amp; REPAIR COMPANY</h2>
      <p>Fast, honest repair for homes and small businesses. We diagnose problems clearly, fix them properly and explain every step, so your computers stay reliable and your work keeps moving without costly surprises.</p>
    </div>
    <div class="hero-photo" role="img" aria-label="Smiling technician in glasses working on an open desktop computer"></div>
  </section>

  <section class="features">
    <div class="feature">
      <div class="icon"><svg width="20" height="20" viewBox="0 0 20 20"><path d="M10 2l7 3v5c0 4-3 7-7 8-4-1-7-4-7-8V5z" fill="none" stroke="#fff" stroke-width="1.6"/></svg></div>
      <h3>Malware Removal</h3><p>Viruses and spyware cleared out safely, with your files kept intact and protection set up.</p><a>Read More »</a>
    </div>
    <div class="feature">
      <div class="icon"><svg width="22" height="20" viewBox="0 0 22 20"><rect x="4" y="4" width="14" height="9" fill="none" stroke="#fff" stroke-width="1.6"/><path d="M1 15h20" stroke="#fff" stroke-width="1.8"/></svg></div>
      <h3>Laptop Hardware Repair</h3><p>Screens, keyboards, batteries and ports replaced with quality parts and quick turnaround.</p><a>Read More »</a>
    </div>
    <div class="feature">
      <div class="icon"><svg width="20" height="20" viewBox="0 0 20 20"><rect x="3" y="3" width="14" height="4" fill="#fff"/><rect x="3" y="8.5" width="14" height="4" fill="#fff"/><rect x="3" y="14" width="14" height="4" fill="#fff"/></svg></div>
      <h3>Data Migration</h3><p>Move files, settings and programs to a new machine without losing a single document.</p><a>Read More »</a>
    </div>
    <div class="feature">
      <div class="icon"><svg width="20" height="20" viewBox="0 0 20 20"><ellipse cx="10" cy="5" rx="6" ry="2.5" fill="#fff"/><path d="M4 5v10c0 1.4 2.7 2.5 6 2.5s6-1.1 6-2.5V5" fill="none" stroke="#fff" stroke-width="1.6"/></svg></div>
      <h3>Data Rescue</h3><p>Recovery from failed drives and damaged storage, handled with care and full privacy.</p><a>Read More »</a>
    </div>
  </section>

  <section class="why">
    <div class="why-art" role="img" aria-label="Cartoon technician holding a wrench beside a desktop computer"></div>
    <div class="why-body">
      <h2 class="title">Why Choose Us</h2>
      <p>We are a local team with years of hands-on experience. Every repair is tested before it leaves our bench, and we give straight answers on cost and timing before any work begins. No jargon, no pressure.</p>
      <ul class="ticks">
        <li>Certified technicians with years of real repair experience</li>
        <li>Clear quotes up front, with no hidden fees or extras</li>
        <li>Quick turnaround for homes and small business clients</li>
        <li>Your data handled privately and returned safely</li>
        <li>Friendly follow-up support after every single repair</li>
      </ul>
    </div>
  </section>

  <section class="about">
    <div class="about-main">
      <h2 class="title">About Our Company</h2>
      <p>Quikbit started with one simple idea: computer repair should be honest, quick and easy to understand. Since then we have helped hundreds of households and small offices keep their machines running smoothly, from single laptops to full office networks.</p>
      <p>We keep our workshop organised, our records tidy and our prices fair. Whether you need a quick virus cleanup or a full hardware rebuild, you can count on careful work and clear communication from the first call to the final check.</p>
      <span class="btn">Learn More</span>
    </div>
    <div class="services">
      <h2 class="title">Our Services</h2>
      <ul>
        <li>Virus Removal</li><li>Malware Removal</li><li>Laptop Hardware Repair</li><li>Upgrades</li><li>Data Migration</li><li>Data Recovery</li><li>Tune Ups</li><li>In Home Installation</li><li>Remote Support</li>
      </ul>
    </div>
  </section>

  <section class="promos">
    <div class="promo">
      <div class="photo" role="img" aria-label="Technician repairing a circuit board at a workbench"></div>
      <div><h4>Repairs done right the first time</h4><p>Each device gets a full diagnostic, a clear written quote and a final quality test. We only replace what is truly needed, saving you time and money.</p></div>
    </div>
    <div class="promo">
      <div class="photo" role="img" aria-label="Technician assembling parts inside an open computer case"></div>
      <div><h4>Support for your small business</h4><p>From setting up new workstations to keeping shared files backed up, we help small offices stay productive with dependable, friendly service.</p></div>
    </div>
  </section>

  <footer class="footer">
    <nav><span>Home</span><span>About Us</span><span>Services</span><span>Features</span><span>Why Choose Us</span><span>Products</span><span>Contact Us</span></nav>
    <div class="round"><i></i><i></i><i></i><i></i><i></i></div>
    <small>© Copyright 2024 Quikbit. All Rights Reserved.</small>
  </footer>
</div>
</body>
</html>
```